Brightlane Rapid Rinse Web Design

We are looking for a web design that highlights our state of the art fully automated commercial vehicle washing equipment. Similar system to a car wash however this system is meant for the largest vehicles on our roadways. Transport trucks with or without a trailer, busses both highway and school, RV's from 5th wheel type to A Class. Cement trucks, dump trucks, vac trucks, fuel trucks etc. Pick ups with utility trailers...Refrigerator truck clean outs.
Brightlane Rapid Rinse will wash your vehicle quickly and with a minimal impact on the environment

Home page
About us
Why Brightlane
Services and pricing
Videos of wash system
Fleets
contact us

Target Market(s)

Commercial vehicle owners and operators as well as corporate fleets. Includes busses, municipal, school and highway.both school and

Industry/Entity Type

transportation

Coding

Coded - Design and coding required

Number of Pages Required

5+ page

Font styles to use
Sans Serif

Colors
0054AA
0677BA
7BADD7
CADEEF
E8F1F8

Requirements
Must have
• Welcome page,why us page which describes the financial and environmental benefits. payment processing page, contact us page, Services which is washing vehicles and greasing for commercial vehicles that want that service and grease
Nice to have
• pictures of both clean and dirty commercial vehicles ie. before and after

```html
<!DOCTYPE html>
<html lang="en">
<head>
<meta charset="utf-8">
<title>Brightlane Rapid Rinse</title>
<link href="https://fonts.googleapis.com/css2?family=Exo+2:wght@400;500;600&family=Mulish:wght@400;600;700&display=swap" rel="stylesheet">
<style>
:root{
  --blue:#0054AA;
  --blue-mid:#0677BA;
  --blue-soft:#7BADD7;
  --blue-pale:#CADEEF;
  --blue-mist:#E8F1F8;
  --ink:#1b1b1b;
  --text:#444;
  --white:#fff;
  --red:#e8413c;
}
*{margin:0;padding:0;box-sizing:border-box}
html,body{width:1200px;height:4967px;overflow:hidden}
body{position:relative;background:var(--white);font-family:'Mulish',sans-serif;color:var(--text)}
.abs{position:absolute}
.heading{font-family:'Exo 2',sans-serif;font-weight:500;text-transform:uppercase;color:var(--ink);font-size:30px;letter-spacing:.5px;text-align:center;left:0;width:1200px}
.dash{position:absolute;left:571px;width:58px;height:3px;background:var(--blue)}
.btn{position:absolute;display:flex;align-items:center;justify-content:center;background:var(--blue);color:var(--white);font-size:12px;font-weight:600;text-transform:uppercase}

/* header */
.topbar{position:absolute;top:0;left:620px;width:450px;height:48px;background:var(--blue);clip-path:polygon(22px 0,100% 0,100% 100%,0 100%);color:var(--white);font-size:12.5px;display:flex;align-items:center;justify-content:flex-end;gap:20px;padding-right:26px}
.topbar span{display:flex;align-items:center;gap:6px}
.top-line{position:absolute;top:0;left:0;width:1200px;height:4px;background:var(--blue)}
.logo{position:absolute;left:131px;top:33px;font-family:'Exo 2',sans-serif;font-weight:500;font-size:26px;line-height:33px;color:var(--ink)}
.nav{position:absolute;top:80px;left:0;font-size:13.5px;color:var(--ink);text-transform:uppercase}
.nav a{position:absolute;white-space:nowrap;text-decoration:none;color:inherit}
.nav a.active{color:var(--blue);font-weight:700}
.nav a.active::after{content:"";position:absolute;left:0;right:0;bottom:-6px;height:2px;background:var(--blue)}

/* hero */
.hero-photo{position:absolute;top:130px;left:0;width:1200px;height:642px;background:linear-gradient(100deg,#5b463c 0%,#8b7a6c 30%,#b9b3a8 55%,#8d7e70 75%,#d8d3cb 100%)}
.hero-title{position:absolute;left:135px;top:228px;font-family:'Exo 2',sans-serif;font-weight:500;font-size:46px;line-height:53px;color:var(--white);text-transform:uppercase;letter-spacing:1px}
.dots{position:absolute;top:659px;left:562px;display:flex;gap:9px}
.dots i{width:13px;height:13px;border-radius:50%;background:var(--white);display:block}
.dots i.on{background:var(--blue)}

/* services */
.card{position:absolute;top:940px;width:301px;height:507px;background:linear-gradient(180deg,#d6e7f3 0%,#eef5fa 70%,#fff 100%)}
.card .photo{width:301px;height:208px;background:linear-gradient(160deg,#7e8791,#c7ccd2 60%,#5f6a78)}
.price{position:absolute;left:185px;top:153px;width:90px;height:90px;border-radius:50%;background:var(--blue);border:4px solid #d6e7f3;color:var(--white);text-align:center;font-family:'Exo 2',sans-serif;font-size:28px;line-height:28px;padding-top:18px}
.price small{display:block;font-family:'Mulish',sans-serif;font-size:10px;line-height:14px}
.card h3{position:absolute;left:35px;top:246px;font-family:'Exo 2',sans-serif;font-weight:400;font-size:24px;line-height:29px;color:var(--blue)}
.card p{position:absolute;left:35px;top:313px;width:240px;font-size:11.5px;line-height:17px;color:#333}
.card .btn{left:35px;top:408px;width:114px;height:34px;font-size:11px}

/* why */
.why-bg{position:absolute;top:1485px;left:0;width:1200px;height:715px;background:linear-gradient(135deg,#0a4fa3 0%,#0a62c0 45%,#0858b3 100%)}
.why-intro{position:absolute;top:1650px;left:200px;width:800px;text-align:center;color:var(--white);font-size:19px;line-height:29px}
.feature{position:absolute;width:230px;text-align:center}
.feature .icon{width:96px;height:96px;margin:0 auto;border-radius:50%;background:var(--blue);border:7px solid var(--white);box-shadow:0 0 0 2px var(--blue-pale);display:flex;align-items:center;justify-content:center}
.feature h4{font-family:'Exo 2',sans-serif;font-weight:400;font-size:19px;color:var(--blue);text-transform:uppercase;margin-top:10px}
.feature p{font-size:12px;line-height:17.5px;color:#333;margin-top:12px}

/* fleets */
.fleet{position:absolute;top:2396px;width:226px}
.fleet .photo{height:231px;background:linear-gradient(170deg,#9ec4e6 0%,#d7e3ec 45%,#8b8f93 100%)}
.fleet span{display:block;text-align:center;margin-top:22px;font-family:'Exo 2',sans-serif;font-size:17px;color:var(--blue);text-transform:uppercase}

/* before after */
.ba{position:absolute;top:2990px;height:310px}
.ba-label{position:absolute;top:3322px;font-size:17px;color:var(--ink);text-transform:uppercase;text-align:center;width:467px}

/* video */
.video{position:absolute;top:3415px;left:0;width:1200px;height:478px;background:linear-gradient(90deg,#6b6f74 0%,#3a3c3e 25%,#2a2c30 50%,#3c3e41 75%,#75797e 100%)}
.play{position:absolute;left:565px;top:3594px;width:70px;height:70px;border-radius:50%;background:var(--red);display:flex;align-items:center;justify-content:center}

/* testimonials */
.testi-bg{position:absolute;top:3893px;left:0;width:1200px;height:760px;background:linear-gradient(180deg,#dcebf2 0%,#f3f8fb 100%)}
.quote-card{position:absolute;top:4074px;width:288px;height:363px;background:var(--white);padding:34px 35px 0}
.quote-card .qm{font-family:'Exo 2',sans-serif;font-weight:600;font-size:52px;line-height:30px;color:var(--blue)}
.quote-card .stars{margin-top:14px;display:flex;gap:2px}
.quote-card p{margin-top:10px;font-size:13px;line-height:19px;color:#555}
.quote-card .rule{margin-top:18px;width:28px;height:2px;background:var(--blue)}
.quote-card b{display:block;margin-top:14px;font-size:12px;color:var(--blue);text-transform:uppercase}

/* footer */
.footer{position:absolute;top:4600px;left:0;width:1200px;height:367px;background:var(--blue)}
.foot-logo{position:absolute;left:129px;top:4712px;font-family:'Exo 2',sans-serif;font-weight:500;font-size:34px;line-height:44px;color:var(--white)}
.foot-col{position:absolute;top:4660px;color:var(--white)}
.foot-col h5{font-size:13px;font-weight:700;text-transform:uppercase;padding-bottom:8px;border-bottom:2px solid var(--white)}
.foot-row{display:flex;align-items:center;gap:10px;font-size:11.5px;line-height:15px;margin-top:20px}
.foot-row i{width:22px;height:22px;border-radius:50%;background:var(--white);flex:none;display:flex;align-items:center;justify-content:center}
.menu-list{list-style:none;font-size:11.5px;line-height:19px;margin-top:12px}
.foot-rule{position:absolute;top:4893px;left:129px;width:942px;height:1px;background:rgba(255,255,255,.35)}
.copyright{position:absolute;top:4926px;left:0;width:1200px;text-align:center;color:var(--white);font-size:11px}
</style>
</head>
<body>

<!-- Header -->
<div class="top-line"></div>
<div class="topbar">
  <span><svg width="12" height="9" viewBox="0 0 12 9"><rect width="12" height="9" rx="1" fill="#fff"/><path d="M0 0 6 5 12 0" stroke="#0054AA" fill="none"/></svg>info@BrightlaneRapidRinse.com</span>
  <span><svg width="11" height="11" viewBox="0 0 24 24"><path fill="#fff" d="M6.6 10.8a15 15 0 0 0 6.6 6.6l2.2-2.2c.3-.3.7-.4 1-.2 1.1.4 2.3.6 3.6.6.6 0 1 .4 1 1V20c0 .6-.4 1-1 1A17 17 0 0 1 3 4c0-.6.4-1 1-1h3.5c.6 0 1 .4 1 1 0 1.3.2 2.5.6 3.6.1.3 0 .7-.2 1z"/></svg>+1 555 010 2030</span>
</div>
<div class="logo">Brightlane<br>Rapid Rinse</div>
<nav class="nav">
  <a class="active" style="left:438px">Home</a>
  <a style="left:520px">About Us</a>
  <a style="left:628px">Services</a>
  <a style="left:731px">Pricing</a>
  <a style="left:828px">Testimonials</a>
  <a style="left:969px">Contact Us</a>
</nav>

<!-- Hero -->
<div class="hero-photo" role="img" aria-label="Worker pressure washing a tanker truck inside a wash bay"></div>
<svg class="abs" style="top:560px;left:0" width="1200" height="215" viewBox="0 0 1200 215">
  <defs>
    <linearGradient id="heroWater" x1="0" y1="0" x2="0" y2="1">
      <stop offset="0" stop-color="#0677BA"/><stop offset=".55" stop-color="#7BADD7"/><stop offset="1" stop-color="#E8F1F8"/>
    </linearGradient>
  </defs>
  <path d="M0 55 C200 10 380 80 600 60 S1000 20 1200 40 V215 H0Z" fill="url(#heroWater)"/>
  <path d="M0 150 C250 120 450 175 700 150 S1050 130 1200 145 V215 H0Z" fill="#f4f8fb"/>
</svg>
<h1 class="hero-title">Speed less than<br>15 minutes and<br>quality</h1>
<div class="btn" style="left:143px;top:425px;width:147px;height:42px;font-size:13px;font-weight:400">Book a Wash</div>
<div class="btn" style="left:301px;top:425px;width:135px;height:42px;font-size:13px;font-weight:400">Learn More</div>
<div class="btn" style="left:448px;top:425px;width:131px;height:42px;font-size:13px;font-weight:400">Contact Us</div>
<div class="dots"><i class="on"></i><i></i><i></i><i></i></div>

<!-- Services and pricing -->
<h2 class="heading abs" style="top:822px">Services and Pricing</h2>
<div class="dash" style="top:893px"></div>

<article class="card" style="left:131px">
  <div class="photo" role="img" aria-label="Semi truck entering an automated wash tunnel"></div>
  <div class="price">$59<small>Per Month</small></div>
  <h3>Automated<br>Truck Wash</h3>
  <p>Lorem ipsum dolor sit amet, conse ctetur adipiscing elit, sed do eiusmod tempor incididunt ut labore et dolore magna aliqua. Ut enim</p>
  <div class="btn">Learn More</div>
</article>
<article class="card" style="left:449px">
  <div class="photo" role="img" aria-label="Trailer passing through blue wash curtains"></div>
  <div class="price">$69<small>Per Month</small></div>
  <h3>Additional<br>Services</h3>
  <p>Lorem ipsum dolor sit amet, conse ctetur adipiscing elit, sed do eiusmod tempor incididunt ut labore et dolore magna aliqua. Ut enim</p>
  <div class="btn">Learn More</div>
</article>
<article class="card" style="left:766px">
  <div class="photo" role="img" aria-label="Worker hand washing a red truck cab"></div>
  <div class="price">$79<small>Per Month</small></div>
  <h3>Fleet<br>Services</h3>
  <p>Lorem ipsum dolor sit amet, conse ctetur adipiscing elit, sed do eiusmod tempor incididunt ut labore et dolore magna aliqua. Ut enim</p>
  <div class="btn">Learn More</div>
</article>

<!-- Why Brightlane -->
<div class="why-bg" role="img" aria-label="Blue tinted close-up of a truck wheel being washed"></div>
<svg class="abs" style="top:1840px;left:0" width="1200" height="375" viewBox="0 0 1200 375">
  <path d="M0 118 C150 80 300 80 450 95 C650 115 800 40 950 20 C1060 8 1140 8 1200 12 V375 H0Z" fill="#fff"/>
  <path d="M0 360 C200 320 400 330 600 350 S1000 370 1200 345 V375 H0Z" fill="#E8F1F8"/>
</svg>
<h2 class="heading abs" style="top:1553px;color:#fff">Why Brightlane</h2>
<div class="dash" style="top:1622px;background:#fff"></div>
<p class="why-intro">Lorem ipsum dolor sit amet, conse ctetur adipiscing elit, sed do eiusmod tempor incididunt ut labore et dolore magna aliqua.</p>
<div class="btn" style="left:525px;top:1748px;width:148px;height:42px;background:#fff;color:var(--blue);font-weight:400;font-size:13px">Book a Wash</div>

<div class="feature" style="left:116px;top:1925px">
  <div class="icon"><svg width="44" height="36" viewBox="0 0 44 36" fill="none" stroke="#fff" stroke-width="2"><rect x="4" y="10" width="22" height="16" rx="2"/><path d="M26 14h8l6 6v6H26"/><circle cx="12" cy="29" r="3"/><circle cx="34" cy="29" r="3"/><path d="M2 4h14M8 8h10"/></svg></div>
  <h4>Speed Wash</h4>
  <p>Lorem ipsum dolor sit amet, conse ctetur adipiscing elit, sed do eius mod tempor incididunt ut labo re et dolore magna .</p>
</div>
<div class="feature" style="left:361px;top:1906px">
  <div class="icon"><svg width="40" height="40" viewBox="0 0 40 40" fill="none" stroke="#fff" stroke-width="2.2"><path d="M8 22v-4a12 12 0 0 1 24 0v4"/><rect x="6" y="20" width="7" height="11" rx="3"/><rect x="27" y="20" width="7" height="11" rx="3"/><path d="M30 31c0 4-4 5-9 5"/></svg></div>
  <h4>Support</h4>
  <p>Lorem ipsum dolor sit amet, conse ctetur adipiscing elit, sed do eius mod tempor incididunt ut labo re et dolore magna .</p>
</div>
<div class="feature" style="left:612px;top:1862px">
  <div class="icon"><svg width="40" height="40" viewBox="0 0 40 40" fill="none" stroke="#fff" stroke-width="2.2"><path d="M12 36V20l6-10c2 0 3 2 2 5l-1 5h9c2 0 3 2 2 4l-3 10c-1 2-2 2-3 2z"/><rect x="4" y="20" width="6" height="16"/><path d="M20 3l1 2 2 .3-1.5 1.4.4 2.3L20 8l-2 1 .4-2.3L17 5.3 19 5z"/></svg></div>
  <h4>Satisfaction</h4>
  <p>Lorem ipsum dolor sit amet, conse ctetur adipiscing elit, sed do eius mod tempor incididunt ut labo re et dolore magna .</p>
</div>
<div class="feature" style="left:853px;top:1856px">
  <div class="icon"><svg width="40" height="40" viewBox="0 0 40 40" fill="none" stroke="#fff" stroke-width="2.2"><path d="M20 3l4 3 5-.5 1.5 4.5 4.5 2-1 5 2 4-3.5 3.5 0 5-5 .5-3 4-4.5-2-4.5 2-3-4-5-.5 0-5L4 21l2-4-1-5 4.5-2L11 5.5l5 .5z"/><path d="M13 20l5 5 9-10"/></svg></div>
  <h4>Quality</h4>
  <p>Lorem ipsum dolor sit amet, conse ctetur adipiscing elit, sed do eius mod tempor incididunt ut labo re et dolore magna .</p>
</div>

<!-- Fleets -->
<div class="abs" style="top:2214px;left:0;width:1200px;height:593px;background:var(--blue-mist)"></div>
<h2 class="heading abs" style="top:2282px">Fleets</h2>
<div class="dash" style="top:2348px"></div>
<div class="fleet" style="left:131px"><div class="photo" role="img" aria-label="White cement mixer truck"></div><span>Cement Trucks</span></div>
<div class="fleet" style="left:370px"><div class="photo" role="img" aria-label="Dump truck with raised bed"></div><span>Dump Trucks</span></div>
<div class="fleet" style="left:606px"><div class="photo" role="img" aria-label="Vacuum tank truck"></div><span>Vac Trucks</span></div>
<div class="fleet" style="left:843px"><div class="photo" role="img" aria-label="Silver fuel tanker truck"></div><span>Fuel Trucks</span></div>
<div class="btn" style="left:530px;top:2718px;width:139px;height:34px;font-size:11px">View All Fleets</div>

<!-- Before and after -->
<h2 class="heading abs" style="top:2870px">Before and After</h2>
<div class="dash" style="top:2939px"></div>
<div class="ba" style="left:131px;width:467px;background:linear-gradient(160deg,#6d6a60,#9a9a94 50%,#c9c6bf)" role="img" aria-label="Dirty tanker truck being sprayed before washing"></div>
<div class="ba" style="left:598px;width:471px;background:linear-gradient(180deg,#e4e7ea 0%,#b7bcc1 45%,#2c4f86 62%,#6f7378 100%)" role="img" aria-label="Clean blue and silver tanker truck after washing"></div>
<div class="abs" style="left:597px;top:2990px;width:3px;height:357px;background:var(--blue)"></div>
<div class="ba-label" style="left:131px">Before</div>
<div class="ba-label" style="left:613px">After</div>
<svg class="abs" style="left:58px;top:3116px" width="26" height="50" viewBox="0 0 26 50"><path d="M24 2 2 25l22 23" fill="none" stroke="#7BADD7" stroke-width="2"/></svg>
<svg class="abs" style="left:1116px;top:3116px" width="26" height="50" viewBox="0 0 26 50"><path d="M2 2l22 23L2 48" fill="none" stroke="#7BADD7" stroke-width="2"/></svg>

<!-- Video -->
<div class="video" role="img" aria-label="Workers washing a truck inside a wash bay"></div>
<div class="play"><svg width="26" height="30" viewBox="0 0 26 30"><path d="M2 1l23 14L2 29z" fill="#fff"/></svg></div>
<h2 class="heading abs" style="top:3703px;color:#fff;font-size:33px">Express Wash System</h2>

<!-- Testimonials -->
<div class="testi-bg"></div>
<h2 class="heading abs" style="top:3951px">Testimonials</h2>
<div class="dash" style="top:4022px"></div>

<div class="quote-card" style="left:131px">
  <div class="qm">&ldquo;</div>
  <div class="stars"><svg width="80" height="14" viewBox="0 0 80 14" fill="#0054AA"><path id="st" d="M7 0l2 4.6 5 .4-3.8 3.3 1.2 4.9L7 10.6 2.6 13.2l1.2-4.9L0 5l5-.4z"/><use href="#st" x="16"/><use href="#st" x="32"/><use href="#st" x="48"/><use href="#st" x="64"/></svg></div>
  <p>Sed ut perspiciatis unde omnis iste natus error sit voluptatem accus antium doloremque lauda ntium, totam rem aperiam, eaque ipsa quae ab illo inventore verit atis et quasi architecto beatae vitae dicta sunt explicabo. Nemo enim ipsam voluptatem quia voluptas.</p>
  <div class="rule"></div><b>Marcus</b>
</div>
<div class="quote-card" style="left:455px">
  <div class="qm">&ldquo;</div>
  <div class="stars"><svg width="80" height="14" viewBox="0 0 80 14" fill="#0054AA"><use href="#st"/><use href="#st" x="16"/><use href="#st" x="32"/><use href="#st" x="48"/><use href="#st" x="64"/></svg></div>
  <p>Sed ut perspiciatis unde omnis iste natus error sit voluptatem accus antium doloremque lauda ntium, totam rem aperiam, eaque ipsa quae ab illo inventore verit atis et quasi architecto beatae vitae dicta sunt explicabo. Nemo enim ipsam voluptatem quia voluptas.</p>
  <div class="rule"></div><b>Marcus</b>
</div>
<div class="quote-card" style="left:779px">
  <div class="qm">&ldquo;</div>
  <div class="stars"><svg width="80" height="14" viewBox="0 0 80 14" fill="#0054AA"><use href="#st"/><use href="#st" x="16"/><use href="#st" x="32"/><use href="#st" x="48"/><use href="#st" x="64"/></svg></div>
  <p>Sed ut perspiciatis unde omnis iste natus error sit voluptatem accus antium doloremque lauda ntium, totam rem aperiam, eaque ipsa quae ab illo inventore verit atis et quasi architecto beatae vitae dicta sunt explicabo. Nemo enim ipsam voluptatem quia voluptas.</p>
  <div class="rule"></div><b>Marcus</b>
</div>
<svg class="abs" style="left:48px;top:4228px" width="26" height="50" viewBox="0 0 26 50"><path d="M24 2 2 25l22 23" fill="none" stroke="#0054AA" stroke-width="3"/></svg>
<svg class="abs" style="left:1120px;top:4228px" width="26" height="50" viewBox="0 0 26 50"><path d="M2 2l22 23L2 48" fill="none" stroke="#0054AA" stroke-width="3"/></svg>

<!-- Footer -->
<svg class="abs" style="top:4440px;left:0" width="1200" height="170" viewBox="0 0 1200 170">
  <defs>
    <linearGradient id="footWater" x1="0" y1="0" x2="0" y2="1">
      <stop offset="0" stop-color="#7BADD7"/><stop offset=".5" stop-color="#0677BA"/><stop offset="1" stop-color="#0054AA"/>
    </linearGradient>
  </defs>
  <path d="M0 40 C200 10 400 70 620 55 S1000 0 1200 20 V170 H0Z" fill="url(#footWater)"/>
  <path d="M0 90 C300 60 550 120 800 95 S1100 75 1200 85 V170 H0Z" fill="#0054AA" opacity=".7"/>
</svg>
<div class="footer"></div>
<div class="foot-logo">Brightlane<br>Rapid Rinse</div>

<div class="foot-col" style="left:438px;width:193px">
  <h5>Contact Us</h5>
  <div class="foot-row"><i><svg width="10" height="12" viewBox="0 0 10 12"><path d="M5 0a4 4 0 0 1 4 4c0 3-4 8-4 8S1 7 1 4a4 4 0 0 1 4-4z" fill="#0054AA"/><circle cx="5" cy="4" r="1.5" fill="#fff"/></svg></i><span>Harbor Row 41,<br>4180 Eastvale</span></div>
  <div class="foot-row"><i><svg width="11" height="11" viewBox="0 0 24 24"><path fill="#0054AA" d="M6.6 10.8a15 15 0 0 0 6.6 6.6l2.2-2.2c.3-.3.7-.4 1-.2 1.1.4 2.3.6 3.6.6.6 0 1 .4 1 1V20c0 .6-.4 1-1 1A17 17 0 0 1 3 4c0-.6.4-1 1-1h3.5c.6 0 1 .4 1 1 0 1.3.2 2.5.6 3.6.1.3 0 .7-.2 1z"/></svg></i><span>Call Us<br>+1 555 010 2030</span></div>
  <div class="foot-row"><i><svg width="11" height="8" viewBox="0 0 12 9"><rect width="12" height="9" rx="1" fill="#0054AA"/><path d="M0 0 6 5 12 0" stroke="#fff" fill="none"/></svg></i><span>E mail Us<br>info@BrightlaneRapidRinse.com</span></div>
</div>

<div class="foot-col" style="left:743px;width:106px">
  <h5>Menu</h5>
  <ul class="menu-list"><li>Home</li><li>About Us</li><li>Services</li><li>Pricing</li><li>Testimonials</li><li>Contact Us</li></ul>
</div>

<div class="foot-col" style="left:957px;width:108px">
  <h5>Follow Us</h5>
  <div class="foot-row"><i></i><span>Like us on<br>CHATTERBOX</span></div>
  <div class="foot-row"><i></i><span>Follow us on<br>LINKWORK</span></div>
  <div class="foot-row"><i></i><span>Follow us on<br>SNAPGRAM</span></div>
</div>

<div class="foot-rule"></div>
<div class="copyright">Copyright © 2024 All Rights Reserved</div>

</body>
</html>
```